self serve frozen yogurt store

would like a postcard to use for promotional purposes. We are a self serve frozen business in Alder Ridge Shopping Center located in Wilmington, DE. We are opened 7 days a week. We offer 15 flavors and over 40 different toppings.

Industry/Entity Type

Store

```html
<!DOCTYPE html>
<html lang="en">
<head>
<meta charset="utf-8">
<title>Larkspur Frozen Yogurt – Postcard</title>
<link rel="stylesheet" href="https://fonts.googleapis.com/css2?family=Fredoka:wght@500;600;700&family=Nunito:wght@500;700;800&display=swap">
<style>
  :root {
    --purple: #7a3f98;
    --purple-dark: #5e2a7e;
    --green: #8cc63f;
    --green-dark: #5f9e1f;
    --orange: #f7941d;
    --white: #ffffff;
    --line: #cfcfcf;
    --stage: #e9e6e1;
  }
  * { box-sizing: border-box; margin: 0; padding: 0; }
  html, body { width: 1200px; height: 900px; overflow: hidden; }
  body { background: var(--stage); font-family: "Nunito", sans-serif; position: relative; }

  .postcard { position: absolute; background: var(--white); overflow: hidden; box-shadow: 0 6px 18px rgba(0,0,0,.18); }

  /* ---------- back side ---------- */
  .postcard--back { left: 30px; top: 30px; width: 570px; height: 420px; }
  .back__header { position: absolute; left: 0; top: 0; width: 420px; height: 130px; }
  .back__contacts { position: absolute; left: 16px; top: 18px; color: var(--white); font-size: 13px; font-weight: 500; list-style: none; }
  .back__contacts li { display: flex; align-items: center; gap: 8px; margin-bottom: 12px; }
  .back__contacts svg { width: 13px; height: 13px; fill: var(--white); }
  .back__photo { position: absolute; left: 0; top: 120px; width: 280px; height: 240px;
    background: radial-gradient(ellipse at 40% 65%, #e9d9d6 0%, #f3f0eb 40%, #e4e0da 75%, #f2f0ec 100%); }
  .back__offer { position: absolute; left: 16px; top: 148px; font-family: "Fredoka", sans-serif; font-weight: 700; line-height: 1; }
  .back__offer .we-offer { color: var(--green); font-size: 19px; display: block; }
  .back__offer .row { display: flex; align-items: flex-end; gap: 2px; }
  .back__offer .amp { color: var(--green-dark); font-size: 24px; line-height: .9; }
  .back__offer .flavors { color: var(--orange); font-size: 18px; }
  .back__offer .toppings { color: var(--purple); font-size: 18px; }
  .back__offer .over { color: var(--purple); font-size: 7px; font-family: "Nunito", sans-serif; margin-right: 3px; }
  .brand-name { font-family: "Nunito", sans-serif; font-weight: 800; color: var(--purple); line-height: 1; }
  .back__brand { position: absolute; left: 150px; top: 326px; font-size: 15px; }
  .stamp-box { position: absolute; right: 22px; top: 14px; width: 110px; height: 118px; border: 1px solid var(--line); }
  .address-lines { position: absolute; left: 300px; top: 188px; width: 240px; }
  .address-lines span { display: block; height: 1px; background: var(--line); margin-bottom: 38px; }

  /* ---------- front side ---------- */
  .postcard--front { left: 600px; top: 440px; width: 570px; height: 430px; background: linear-gradient(#eceae8, var(--white) 40%); }
  .front__brand { position: absolute; left: 22px; top: 62px; font-size: 34px; }
  .front__hours { position: absolute; right: 26px; top: 28px; font-family: "Fredoka", sans-serif; font-weight: 700; line-height: .9; text-align: right; }
  .front__hours .opened { color: var(--purple); font-size: 26px; display: block; text-align: left; }
  .front__hours .days { color: var(--green); font-size: 44px; display: block; }
  .front__hours .week { color: var(--orange); font-size: 24px; display: block; }
  .front__photo { position: absolute; left: 276px; top: 150px; width: 284px; height: 236px; border-radius: 10px;
    background: radial-gradient(ellipse at 50% 45%, #f3d9e6 0%, #f6f1ea 35%, #e6dfd6 65%, #f4f2ef 100%); }
  .front__info { position: absolute; left: 22px; top: 190px; }
  .front__address { font-family: "Nunito", sans-serif; font-weight: 800; color: var(--purple); font-size: 16px; line-height: 1.3; }
  .front__phone { display: flex; align-items: center; gap: 6px; color: var(--orange); font-family: "Nunito", sans-serif; font-weight: 800; font-size: 24px; margin-top: 10px; }
  .front__phone svg { width: 16px; height: 16px; fill: var(--orange); }
  .front__social { display: flex; align-items: center; gap: 8px; margin-top: 8px; }
  .front__social .square { width: 36px; height: 36px; background: var(--purple-dark); }
  .front__social p { font-family: "Nunito", sans-serif; font-weight: 800; color: var(--green); font-size: 18px; line-height: 1.05; }
  .front__bands { position: absolute; left: 0; bottom: 0; width: 570px; height: 70px; }
</style>
</head>
<body>

<section class="postcard postcard--back" aria-label="Postcard back">
  <svg class="back__header" viewBox="0 0 420 130" aria-hidden="true">
    <path d="M0 0 H420 C360 70 250 120 0 118 Z" fill="var(--purple)"/>
  </svg>
  <ul class="back__contacts">
    <li><svg viewBox="0 0 16 16"><path d="M8 1 1 8h2v7h4v-4h2v4h4V8h2z"/></svg>2190 Hollow Pine Road Wilmington, DE 19808</li>
    <li><svg viewBox="0 0 16 16"><path d="M4 1 2 3c0 6 5 12 11 12l2-2-3-3-2 1C8 10 6 8 5 6l1-2z"/></svg>(302) 555-0148</li>
    <li><svg viewBox="0 0 16 16"><circle cx="8" cy="8" r="6.5" fill="none" stroke="#fff" stroke-width="1.3"/><path d="M1.5 8h13M8 1.5c-3 3.5-3 9.5 0 13M8 1.5c3 3.5 3 9.5 0 13" fill="none" stroke="#fff" stroke-width="1.1"/></svg>www.larkspuryogurt.com</li>
  </ul>
  <div class="back__photo" role="img" aria-label="Photo of a strawberry splashing into milk"></div>
  <div class="back__offer">
    <span class="we-offer">We offer</span>
    <div class="row"><span class="amp">&amp;</span><span class="flavors">15 flavors</span></div>
    <div class="row"><span class="over">OVER</span><span class="toppings">40 different toppings.</span></div>
  </div>
  <p class="brand-name back__brand">Larkspur Frozen Yogurt</p>
  <div class="stamp-box" aria-hidden="true"></div>
  <div class="address-lines" aria-hidden="true"><span></span><span></span><span></span><span></span></div>
</section>

<section class="postcard postcard--front" aria-label="Postcard front">
  <p class="brand-name front__brand">Larkspur Frozen Yogurt</p>
  <div class="front__hours">
    <span class="opened">opened</span>
    <span class="days">7 days</span>
    <span class="week">a week</span>
  </div>
  <div class="front__photo" role="img" aria-label="Photo of frozen yogurt cups topped with fruit, strawberries and blueberries"></div>
  <div class="front__info">
    <p class="front__address">Alder Ridge Shopping Center<br>Wilmington, DE 19808</p>
    <p class="front__phone"><svg viewBox="0 0 16 16"><path d="M4 1 2 3c0 6 5 12 11 12l2-2-3-3-2 1C8 10 6 8 5 6l1-2z"/></svg>302-555-0148</p>
    <div class="front__social"><span class="square"></span><p>check us out<br>on Pinwall</p></div>
  </div>
  <svg class="front__bands" viewBox="0 0 570 70" preserveAspectRatio="none" aria-hidden="true">
    <path d="M0 4 C150 30 350 48 570 22 V70 H0 Z" fill="var(--orange)"/>
    <path d="M0 12 C150 38 350 54 570 30 V70 H0 Z" fill="var(--green)"/>
    <path d="M0 24 C150 48 350 62 570 40 V70 H0 Z" fill="var(--purple)"/>
  </svg>
</section>

</body>
</html>
```